Wine Shop Banners

Banner graphic/images required
Require banner images to match the present online wine shop.

www.velmora-weinhaus.de

The wine-shop presently has a very clean, simple design, lots of white space, which is very much the trend at the moment.

Requirements
Images or graphic design for present banners visible on the homepage

The colour and feeling of the banners must fit in with the present clean, simple design.

Work required
3 large slide-card/banners (can be more) and 3 smaller fixed banners below. Please view website to see present position of banners.

LARGE BANNERS x 3

Something special with white background within the banner space
White background on each slide-card. Small individual graphic image in the middle of the slide card. This could be either a simple element of wine:
ingredients, fruit (grape), bottle, cork, old bottle label etc. just displaying one item on each slide-card. Preferably with high quality graphic features.

Note:
We are trying the steer away from the classic stereotype wineshop design. The image/s should have a higher, individual graphic touch, which gives the design something different. Sometimes such artistic work is displayed in steampunk or even in nostalgic design, which leaves the viewer slightly memorized with the content.
To clarify: we are not looking for a full steampunk design but possibly certain elements of this will give you an idea what we mean. That is to say, the design can go slightly in this direction without going over the top. Something small but very eye-catching.

SMALLER BANNERS x 3

One idea is:
Showing a symbol e.g. - discount sign "%" against a white background but again with a high graphic quality.

Target Market(s)

People interested in purchasing wine.
Ages approx. 25 to 65

Industry/Entity Type

Shop

Requirements
Must have
• Something special with white background
• Small individual graphic image in the middle of the slide card.
Nice to have
• The image/s should have a higher, individual graphic touch, which gives the design something different. Something that leaves the viewer slightly memorized with the content.
Should not have
• Not the typical classical design that is often seen on wine shops.

```html
<!DOCTYPE html>
<html lang="de">
<head>
<meta charset="utf-8">
<title>Velmora Weinhaus – Weinshop</title>
<link rel="stylesheet" href="https://fonts.googleapis.com/css2?family=Open+Sans:wght@300;400;600&family=Playfair+Display:ital@1&family=Alex+Brush&family=Noto+Serif:wght@400&display=swap">
<style>
:root{
  --wine:#b5174a;
  --wine-dark:#5e1010;
  --olive:#4f5a2c;
  --lime:#d3dc5e;
  --lime-text:#c6d24a;
  --text:#555;
  --muted:#999;
  --line:#e6e6e6;
  --taupe:#c7b89c;
  --brown:#7a6a57;
  --white:#fff;
}
*{margin:0;padding:0;box-sizing:border-box}
html,body{width:1200px;height:748px;overflow:hidden;background:var(--white)}
body{position:relative;font-family:"Open Sans",sans-serif;color:var(--text)}
.abs{position:absolute}
.brand{left:34px;top:34px;font-family:"Open Sans",sans-serif;font-weight:600;color:var(--olive);font-size:40px;line-height:1;letter-spacing:1px}
.brand small{display:block;font-size:15px;font-weight:600;letter-spacing:7px;margin-top:14px}
.search{left:592px;top:52px;width:314px;height:36px;border:1px solid #bbb;display:flex}
.search svg{margin:10px 12px 0 12px}
.search span{flex:1;font-size:14px;color:#666;line-height:34px}
.search b{width:46px;background:var(--wine);color:#fff;font-weight:400;font-size:15px;text-align:center;line-height:34px}
.account{left:1011px;top:40px;font-size:17px;font-weight:300;color:#666;display:flex;gap:16px;align-items:center}
.nav{left:52px;top:138px;display:flex;font-size:17px;font-weight:300;color:#666}
.nav span{margin-right:40px}
.badge{width:19px;height:19px;border-radius:50%;background:#c2c81a;color:#fff;font-size:11px;text-align:center;line-height:19px}
.filter-title{left:33px;top:181px;width:233px;height:38px;background:var(--lime);color:#5a5a3a;font-size:15px;font-weight:600;padding:9px 0 0 14px}
.group{left:36px;font-size:15px;font-weight:600;color:var(--lime-text)}
.list{left:36px;font-size:15px;font-weight:300;color:#555;overflow:hidden}
.list li{list-style:none;height:25px;line-height:25px}
.list li::before{content:"›";margin-right:9px;font-weight:600}
.list em{font-style:normal;color:var(--muted)}
.scroll{left:250px;top:267px;width:14px;height:180px;background:#eee}
.scroll i{position:absolute;left:1px;top:12px;width:12px;height:78px;background:#c4c4c4}
.hero{left:279px;top:179px;width:866px;height:341px;box-shadow:0 0 6px rgba(0,0,0,.12);background:#fff}
.hero-title{position:absolute;left:72px;top:78px;font-family:"Alex Brush",cursive;color:var(--wine-dark);font-size:92px;line-height:.85;transform:rotate(-4deg)}
.hero-title span{display:block;padding-left:46px}
.hero-photo{position:absolute;right:0;top:0;width:340px;height:341px;background:radial-gradient(ellipse 60% 55% at 42% 62%,#b0203a 0,#d890a0 30%,#f4ece6 62%,#fff 85%)}
.dots{position:absolute;left:774px;top:300px;display:flex;gap:12px}
.dots i{width:19px;height:19px;border-radius:50%;background:#fff;box-shadow:0 1px 4px rgba(0,0,0,.35)}
.promo{top:530px;width:282px;height:133px;overflow:hidden;background:linear-gradient(90deg,#e4e4e4,#fafafa)}
.promo svg.cut{position:absolute;left:0;top:0}
.promo .lead{position:absolute;font-family:"Playfair Display",serif;font-style:italic;color:#6e6250;line-height:1.25}
.promo .big{position:absolute;font-family:"Playfair Display",serif;font-style:italic;color:#fff;line-height:1}
.promo .go{position:absolute;right:10px;bottom:10px}
.promo-photo{position:absolute;left:0;top:0;width:180px;height:133px;background:linear-gradient(135deg,#b9ad9a,#e6e0d6 55%,#fafafa)}
.featured{left:278px;top:686px;font-family:"Noto Serif",serif;font-size:17px;color:#333;display:flex;gap:10px;align-items:center}
.pager{left:1101px;top:685px;display:flex;gap:5px}
.pager i{width:20px;height:21px;border:1px solid #999;display:flex;align-items:center;justify-content:center}
.rule{left:274px;top:717px;width:878px;height:3px;background:#eee}
.card{top:722px;width:218px;height:30px;border:1px solid var(--line)}
</style>
</head>
<body>

<div class="abs brand">VELMORA<small>WEINHAUS</small></div>

<div class="abs search">
  <svg width="16" height="16" viewBox="0 0 16 16"><circle cx="6.5" cy="6.5" r="4.5" fill="none" stroke="#b5174a" stroke-width="2"/><path d="M10 10l4 4" stroke="#b5174a" stroke-width="2.4"/></svg>
  <span>Suche</span><b>GO</b>
</div>

<div class="abs account">Abmelden
  <svg width="26" height="30" viewBox="0 0 26 30"><circle cx="13" cy="9" r="6.5" fill="none" stroke="#777" stroke-width="1.8"/><path d="M2 28c0-8 5-11 11-11s11 3 11 11z" fill="none" stroke="#777" stroke-width="1.8" stroke-linejoin="round"/></svg>
</div>

<nav class="abs nav"><span>Rotwein</span><span>Weißwein</span><span>Rosewein</span><span>Sekt / Champagner</span><span>Sonderangebote</span><span>Probierpakete</span></nav>

<svg class="abs" style="left:1046px;top:134px" width="32" height="28" viewBox="0 0 32 28"><path d="M1 3h5l4 16h16l3-11H8" fill="none" stroke="#888" stroke-width="2" stroke-linejoin="round"/><circle cx="12" cy="24" r="2" fill="#888"/><circle cx="24" cy="24" r="2" fill="#888"/></svg>
<div class="abs badge" style="left:1067px;top:126px">0</div>
<svg class="abs" style="left:1106px;top:130px" width="34" height="34" viewBox="0 0 34 34"><circle cx="17" cy="17" r="17" fill="#8a8a8a"/><path d="M17 24l-7-7a4 4 0 016-5l1 1 1-1a4 4 0 016 5z" fill="none" stroke="#fff" stroke-width="1.8"/></svg>
<div class="abs badge" style="left:1128px;top:126px">0</div>

<div class="abs filter-title">DETAILSUCHE</div>

<div class="abs group" style="top:235px">LAND</div>
<ul class="abs list" style="top:266px;height:180px">
  <li>Italien <em>(87)</em></li><li>Frankreich <em>(74)</em></li><li>Deutschland <em>(58)</em></li><li>Spanien <em>(35)</em></li><li>Südafrika <em>(15)</em></li><li>Österreich <em>(12)</em></li><li>Australien <em>(12)</em></li><li>Portugal <em>(10)</em></li>
</ul>
<div class="abs scroll"><i></i></div>

<div class="abs group" style="top:471px">GESCHMACK</div>
<ul class="abs list" style="top:503px">
  <li>Trocken <em>(303)</em></li><li>Halbtrocken <em>(8)</em></li><li>Lieblich <em>(5)</em></li><li>Süß <em>(3)</em></li><li>Edelsüss <em>(1)</em></li>
</ul>

<div class="abs group" style="top:651px">FARBE</div>
<ul class="abs list" style="top:683px">
  <li>Rot <em>(155)</em></li><li>Weiß <em>(127)</em></li>
</ul>

<section class="abs hero">
  <div class="hero-title">Best of<span>Friends</span></div>
  <div class="hero-photo" role="img" aria-label="Zwei anstoßende Weingläser mit spritzendem Rot- und Weißwein"></div>
  <div class="dots"><i></i><i></i><i></i></div>
</section>

<div class="abs promo" style="left:278px">
  <svg class="cut" width="282" height="133"><polygon points="182,0 282,0 282,133 105,133" fill="var(--taupe)"/></svg>
  <div class="lead" style="left:26px;top:24px;font-size:22px">free shipping<br>on orders<br>over</div>
  <div class="big" style="left:158px;top:44px;font-size:70px">$25</div>
  <svg class="go" width="22" height="22"><circle cx="11" cy="11" r="10" fill="#fff"/><path d="M8 6l7 5-7 5z" fill="var(--taupe)"/></svg>
</div>

<div class="abs promo" style="left:571px">
  <div class="promo-photo" role="img" aria-label="Herausspringender Sektkorken mit perlendem Schaum"></div>
  <svg class="cut" width="282" height="133"><polygon points="182,0 282,0 282,133 105,133" fill="var(--brown)"/></svg>
  <div class="big" style="left:153px;top:52px;font-size:32px;line-height:1.05">celebrate<br>in style</div>
  <svg class="go" width="22" height="22"><circle cx="11" cy="11" r="10" fill="#fff"/><path d="M8 6l7 5-7 5z" fill="var(--brown)"/></svg>
</div>

<div class="abs promo" style="left:864px">
  <svg class="cut" width="282" height="133"><polygon points="182,0 282,0 282,133 105,133" fill="var(--brown)"/></svg>
  <div class="lead" style="left:26px;top:38px;font-size:38px;line-height:.95">special<br>offers</div>
  <div class="lead" style="left:170px;top:26px;font-size:20px;color:#fff">save up to</div>
  <div class="big" style="left:148px;top:56px;font-size:62px">35%</div>
  <svg class="go" width="22" height="22"><circle cx="11" cy="11" r="10" fill="#fff"/><path d="M8 6l7 5-7 5z" fill="var(--brown)"/></svg>
</div>

<div class="abs featured">
  <svg width="20" height="20"><circle cx="10" cy="10" r="9" fill="none" stroke="#b5174a" stroke-width="1.5"/><path d="M8 6l6 4-6 4z" fill="#b5174a"/></svg>
  Ausgewählte Produkte
</div>
<div class="abs pager">
  <i><svg width="8" height="12"><path d="M7 1L2 6l5 5" fill="none" stroke="#555" stroke-width="1.5"/></svg></i>
  <i><svg width="8" height="12"><path d="M1 1l5 5-5 5" fill="none" stroke="#555" stroke-width="1.5"/></svg></i>
</div>
<div class="abs rule"></div>
<div class="abs card" style="left:274px"></div>
<div class="abs card" style="left:494px"></div>
<div class="abs card" style="left:714px"></div>
<div class="abs card" style="left:934px"></div>

</body>
</html>
```